Specialised investor in e-mobility and energy wants business card design

We need a business card design that fits our existing corporate design. <The look and feel must be 'sharp'/'clean', dynamic, communicate momentum, professionalism etc (as one would imagine from a firm in the financial sector). We like the idea of a reverse-side of the card that includes the logo, and the name and contact details on the other. We expect the deliverable to be whatever format might be required to be able to get cards printed directly by a service such as kelmo press. Our website is www.zub.capital

```html
<!DOCTYPE html>
<html lang="en">
<head>
<meta charset="utf-8">
<title>ZUB Capital business card</title>
<link href="https://fonts.googleapis.com/css2?family=Montserrat:wght@400;500;700&display=swap" rel="stylesheet">
<style>
  :root {
    --stage: #1f2020;
    --green-dark: #2f5322;
    --green-mid: #3b6229;
    --green-light: #8cc43f;
    --paper: #ffffff;
  }
  html, body { margin: 0; padding: 0; overflow: hidden; }
  body {
    width: 1200px; height: 801px;
    background: var(--stage);
    font-family: "Montserrat", Arial, sans-serif;
    display: flex; align-items: center; justify-content: center; gap: 40px;
  }
  .card {
    position: relative;
    width: 540px; height: 309px;
    border-radius: 22px;
    overflow: hidden;
    box-shadow: 0 0 0 3px var(--green-light);
  }
  .card-front { background: var(--paper); }
  .front-wave { position: absolute; inset: 0; width: 100%; height: 100%; }
  .brand {
    position: absolute; top: 24px; right: 40px;
    font-weight: 500; font-size: 40px; letter-spacing: 1px; line-height: 1.1;
    color: var(--green-dark); margin: 0;
  }
  .address {
    position: absolute; right: 28px; top: 150px;
    text-align: right; color: var(--paper); font-size: 12px; line-height: 1.5; margin: 0;
  }
  .person { position: absolute; left: 28px; bottom: 18px; color: var(--paper); }
  .person-name { margin: 0; font-weight: 700; font-size: 19px; line-height: 1.15; color: var(--green-light); }
  .person-role { margin: 1px 0 8px; font-size: 12px; line-height: 1.25; }
  .contact-list { list-style: none; margin: 0; padding: 0; font-size: 12px; line-height: 1.3; }
  .contact-list li { display: flex; align-items: center; gap: 7px; margin-top: 3px; }
  .contact-list svg { width: 11px; height: 11px; flex: none; }
  .icon-fill { fill: var(--green-light); }
  .icon-line { fill: none; stroke: var(--green-light); stroke-width: 2.5; }
  .card-back { background: var(--green-mid); }
  .back-pattern {
    position: absolute; inset: 0;
    background: linear-gradient(135deg, #34591f 0%, #3f682b 55%, #33571f 100%);
  }
  .back-brand {
    position: absolute; right: 48px; bottom: 74px;
    color: var(--paper); font-weight: 700; font-size: 28px; letter-spacing: 2px; margin: 0;
  }
</style>
</head>
<body>
  <section class="card card-front">
    <svg class="front-wave" viewBox="0 0 540 309" preserveAspectRatio="none" aria-hidden="true">
      <path d="M0 160 C40 120 200 145 330 120 S510 100 540 62 L540 309 L0 309 Z" fill="var(--green-light)"/>
      <path d="M0 172 C40 132 200 157 330 132 S512 114 540 78 L540 309 L0 309 Z" fill="var(--green-dark)"/>
    </svg>
    <p class="brand">ZUB capital</p>
    <p class="address">1234 Street Name<br>Country Name AB 5748</p>
    <div class="person">
      <p class="person-name">Marek Olden</p>
      <p class="person-role">Director/Founder</p>
      <ul class="contact-list">
        <li><svg viewBox="0 0 24 24"><path class="icon-fill" d="M6.6 10.8a15 15 0 0 0 6.6 6.6l2.2-2.2a1 1 0 0 1 1-.25 11.4 11.4 0 0 0 3.6.57 1 1 0 0 1 1 1V20a1 1 0 0 1-1 1A17 17 0 0 1 3 4a1 1 0 0 1 1-1h3.5a1 1 0 0 1 1 1c0 1.25.2 2.45.57 3.57a1 1 0 0 1-.25 1z"/></svg>123-480-2291</li>
        <li><svg viewBox="0 0 24 24"><path class="icon-line" d="M3 5h18v14H3z M3 5l9 8 9-8"/></svg>info@zub.capital</li>
        <li><svg viewBox="0 0 24 24"><circle class="icon-line" cx="12" cy="12" r="9"/></svg>www.zub.capital</li>
      </ul>
    </div>
  </section>

  <section class="card card-back">
    <div class="back-pattern" role="img" aria-label="Repeating brand mark pattern in tonal green"></div>
    <p class="back-brand">ZUB</p>
  </section>
</body>
</html>
```